Vorelan.com Personal Trainer/Fitness Website

I want a website to market my personal training/Outdoor Bootcamp Class services, as well as to ditribute nutrivex. I need a logo as well I included an address for the Harbor Gales 1975 logo. I'd like Vorelan in place of Harbor Gales, and in Black and white, just different enough so I can't get sued by the PBL.
https://www.pictofind.example/imgres?imgurl=http%3A%2F%2Fwww.darnell-quibury.example%2Fwp-content%2Fuploads%2F2014%2F01%2Fgales_logo4.jpg&imgrefurl=http%3A%2F%2Fwww.darnell-quibury.example%2Fpbl-logo-redesigns-harbor-gales%2F&docid=_qkwzR7TBAgXpL&tbnid=m4tpU8KdOXjnRP%3A&w=600&h=450&client=ms-android-carrier&bih=512&biw=360&ved=0ahUKEwiRtpgyp9HMAhUTwGMKHRPMBWMQMwg6KBQwFA&iact=mrc&uact=8.
It should be about 5 pages 1. home 2. about 3. Services 4. Blog/Videos and programs 5. Contact.
http://www.dorvinfitness.example.uk/ is a website I like the style of.

Target Market(s)

Seattle area

Industry/Entity Type

Fitness

Coding

Coded - Design and coding required

Number of Pages Required

4 page

Font styles to use
Serif
Sans Serif

Requirements
Must have
• A minimal look
Nice to have
• A logo similar to the 1975 Harbor Galewinds Logo, with a Small Milo Brandt ripping his shirt open(with a picture of the logo on his shirt, picture within picture) to turn into Ironjaw in the center. Skyline is black, Background and small figure white(with black logo on shirt)

```html
<!DOCTYPE html>
<html lang="en">
<head>
<meta charset="utf-8">
<title>Vorelan – Personal Training</title>
<link rel="stylesheet" href="https://fonts.googleapis.com/css2?family=Arimo:wght@400;700&family=Open+Sans:ital,wght@0,400;0,600;0,700;1,400&display=swap">
<style>
:root{
  --green:#0b6b3a;
  --green-dark:#08552e;
  --ink:#2b2b2b;
  --muted:#6f6f6f;
  --light:#9a9a9a;
  --rule:#e3e3e3;
  --hero:#0e0e0e;
  --band:#151515;
  --footer:#1b1b1b;
  --star:#f5b400;
  --white:#ffffff;
}
*{box-sizing:border-box;margin:0;padding:0}
html,body{width:1200px;height:3087px;overflow:hidden}
body{font-family:"Open Sans",Arial,sans-serif;color:var(--ink);background:var(--white);position:relative}
.heading{font-family:"Arimo",Arial,sans-serif;font-weight:700}
a{color:inherit;text-decoration:none}

/* header */
.site-header{height:86px;position:relative;background:var(--white);box-shadow:0 1px 4px rgba(0,0,0,.08);z-index:2}
.brand{position:absolute;left:100px;top:14px;display:flex;align-items:center;gap:10px}
.brand-dot{width:44px;height:44px;border-radius:50%;background:var(--green)}
.brand-name{font-family:"Arimo",Arial,sans-serif;font-weight:700;font-size:24px;color:var(--ink)}
.callbar{position:absolute;right:100px;top:14px;display:flex;align-items:center;gap:8px}
.callbar .label{font-size:11px;font-weight:600;color:#444}
.callbar .number{font-size:17px;font-weight:700;color:var(--green)}
.main-nav{position:absolute;right:100px;top:58px;display:flex;gap:30px;align-items:center}
.main-nav a{font-family:"Arimo",Arial,sans-serif;font-weight:700;font-size:13px;color:#222;padding-bottom:6px}
.main-nav a.active{color:var(--green);border-bottom:2px solid var(--green)}

/* hero */
.hero{height:497px;position:relative;background:linear-gradient(90deg,#080808 0%,#161616 55%,#1c1c1c 100%);overflow:hidden}
.hero-photo{position:absolute;right:0;top:0;width:420px;height:497px;background:radial-gradient(ellipse at 55% 40%,#8a7560 0%,#4a3d33 35%,#1a1816 75%,#111 100%)}
.hero-copy{position:absolute;left:100px;top:150px;color:var(--white)}
.hero-title{font-size:62px;line-height:72px}
.hero-sub{font-size:28px;line-height:36px;margin-top:4px;font-weight:400}
.hero-actions{display:flex;gap:20px;margin-top:22px}
.btn{display:inline-flex;align-items:center;justify-content:center;font-family:"Arimo",Arial,sans-serif;font-weight:700;font-size:15px;text-transform:uppercase;height:48px}
.btn-green{background:var(--green);color:var(--white)}
.btn-outline{border:3px solid var(--white);color:var(--white)}
.hero .btn{width:178px}
.hero-dots{position:absolute;left:532px;top:437px;display:flex;gap:6px}
.hero-dots span{width:30px;height:5px;border-radius:3px;background:var(--white)}
.hero-dots span.on{background:var(--green)}

/* services */
.services{height:429px;padding-top:48px;text-align:center}
.section-title{font-size:27px;color:#2a2a2a;letter-spacing:.3px}
.section-sub{font-size:17px;color:var(--muted);margin-top:14px}
.service-grid{width:1030px;margin:34px auto 0;display:grid;grid-template-columns:repeat(4,1fr)}
.service-icon{width:116px;height:116px;border-radius:50%;background:var(--green);border:4px solid var(--white);box-shadow:0 0 0 2px var(--green);margin:0 auto;display:flex;align-items:center;justify-content:center}
.service-name{font-family:"Arimo",Arial,sans-serif;font-weight:700;font-size:15px;margin-top:20px;color:#222}
.service-text{font-size:12px;line-height:20px;color:var(--light);width:230px;margin:8px auto 0}
.read-more{display:block;font-family:"Arimo",Arial,sans-serif;font-weight:700;font-size:12px;color:var(--green);margin-top:16px}
.divider{width:1000px;height:1px;background:var(--rule);margin:41px auto 0}

/* features */
.features{height:812px;padding-top:48px}
.feature-row{width:1000px;height:352px;margin:0 auto;display:flex}
.feature-photo{width:500px;height:352px}
.photo-pushup{background:linear-gradient(135deg,#d9d4ce 0%,#a9a39c 45%,#4a4744 100%)}
.photo-couple{background:radial-gradient(ellipse at 50% 45%,#6a5244 0%,#2c2320 45%,#050505 80%)}
.feature-copy{width:500px;padding:10px 0 0 38px}
.feature-row.reverse .feature-copy{padding:20px 38px 0 0}
.feature-title{font-size:27px;color:#2a2a2a}
.feature-text{font-size:12px;line-height:24px;color:var(--light);margin-top:14px}
.tick-list{list-style:none;margin-top:18px}
.tick-list li{display:flex;align-items:center;gap:10px;font-size:12px;line-height:26px;color:#666}
.feature-copy .btn{width:182px;margin-top:22px;height:50px}

/* feedback */
.feedback{height:326px;position:relative;background:var(--band);color:var(--white)}
.feedback-bg{position:absolute;inset:0;background:radial-gradient(ellipse at 18% 45%,#3a3330 0%,#1a1818 40%,#0d0d0d 80%)}
.feedback-inner{position:relative;padding-top:46px;text-align:center}
.feedback .section-title{color:var(--white)}
.quotes{width:1010px;margin:26px auto 0;display:grid;grid-template-columns:repeat(3,1fr);gap:22px;text-align:left}
.quote{display:flex;gap:18px}
.avatar{flex:none;width:76px;height:76px;border-radius:50%;background:linear-gradient(160deg,#cbbfb4,#7d736c);border:3px solid var(--white)}
.stars{display:flex;gap:2px}
.quote-text{font-style:italic;font-size:12px;line-height:21px;color:#e8e8e8;margin-top:6px}
.quote-name{font-family:"Arimo",Arial,sans-serif;font-weight:700;font-size:12px;margin-top:12px}
.slider-arrows{position:absolute;left:553px;top:303px;display:flex;gap:4px;z-index:1}
.slider-arrows span{width:46px;height:46px;border-radius:50%;background:var(--white);box-shadow:0 1px 4px rgba(0,0,0,.25);display:flex;align-items:center;justify-content:center}

/* blog */
.blog{height:620px;padding-top:64px;text-align:center}
.post-grid{width:1004px;margin:30px auto 0;display:grid;grid-template-columns:repeat(3,1fr);gap:18px;text-align:left}
.post-photo{height:218px;position:relative}
.photo-gym{background:linear-gradient(135deg,#b9b3ad 0%,#5c5753 55%,#2a2826 100%)}
.photo-class{background:linear-gradient(180deg,#c7c2be 0%,#a05b5b 55%,#3a3a4a 100%)}
.photo-outdoor{background:linear-gradient(180deg,#9fb7cf 0%,#c88a5a 50%,#6e5a3a 100%)}
.post-date{position:absolute;right:0;bottom:0;background:rgba(0,0,0,.7);color:var(--white);font-size:13px;font-weight:600;padding:6px 10px;display:flex;gap:6px;align-items:center}
.post-title{font-size:18px;color:#222;margin-top:18px}
.post-text{font-size:12px;line-height:22px;color:var(--light);margin-top:10px}
.blog .read-more{margin-top:14px}
.blog .btn{width:186px;margin-top:34px;height:48px}

/* footer */
.site-footer{height:316px;background:var(--footer);color:var(--white);position:relative}
.footer-brand{position:absolute;left:116px;top:44px;text-align:center;width:200px}
.footer-brand .mark{width:150px;height:150px;border-radius:50%;background:var(--green);margin:0 auto}
.footer-brand .name{font-family:"Arimo",Arial,sans-serif;font-weight:700;font-size:40px;margin-top:4px}
.footer-col{position:absolute;top:40px}
.footer-col h4{font-size:16px;letter-spacing:.3px}
.footer-col ul{list-style:none;margin-top:20px}
.footer-col li{font-size:12px;line-height:25px}
.col-info{left:387px}
.col-news{left:583px;width:270px}
.col-news p{font-size:12px;line-height:20px;margin-top:20px}
.news-input{width:262px;height:34px;background:var(--white);margin-top:14px;color:#999;font-size:12px;padding:9px 10px}
.news-btn{display:inline-block;border:2px solid var(--white);font-family:"Arimo",Arial,sans-serif;font-weight:700;font-size:12px;padding:8px 10px;margin-top:16px}
.col-contact{left:911px;width:210px}
.contact-line{display:flex;gap:14px;font-size:12px;line-height:20px;margin-top:22px}
.contact-line svg{flex:none;margin-top:3px}
.copyright{position:absolute;left:100px;top:279px;font-size:11px;color:#ddd}
.social{position:absolute;left:893px;top:263px;display:flex;gap:8px}
.social span{width:34px;height:34px;border-radius:50%;border:2px solid var(--white)}
</style>
</head>
<body>

<header class="site-header">
  <a class="brand" href="#"><span class="brand-dot"></span><span class="brand-name">Vorelan</span></a>
  <div class="callbar">
    <svg width="22" height="22" viewBox="0 0 22 22"><circle cx="11" cy="11" r="10" fill="none" stroke="#0b6b3a" stroke-width="1.5"/><path d="M7.5 6.5l2 0 1 2.5-1.3 1a6 6 0 0 0 2.8 2.8l1-1.3 2.5 1v2a1 1 0 0 1-1 1A8 8 0 0 1 6.5 7.5a1 1 0 0 1 1-1z" fill="#0b6b3a"/></svg>
    <span class="label">CALL US TODAY :</span>
    <span class="number">1 888 555 0142</span>
  </div>
  <nav class="main-nav">
    <a class="active" href="#">HOME</a><a href="#">ABOUT</a><a href="#">SERVICES</a><a href="#">BLOG</a><a href="#">VIDEOS</a><a href="#">CONTACT</a>
    <svg width="14" height="14" viewBox="0 0 14 14"><circle cx="6" cy="6" r="4.5" fill="none" stroke="#222" stroke-width="2"/><path d="M9.3 9.3l3.5 3.5" stroke="#222" stroke-width="2"/></svg>
  </nav>
</header>

<section class="hero">
  <div class="hero-photo" role="img" aria-label="Athletic blonde woman in a black sports top, seen in profile"></div>
  <div class="hero-copy">
    <h1 class="hero-title heading">Vorelan</h1>
    <p class="hero-sub">We are a personal training class services</p>
    <div class="hero-actions">
      <a class="btn btn-green" href="#">Get in touch</a>
      <a class="btn btn-outline" href="#">Read more</a>
    </div>
  </div>
  <div class="hero-dots"><span class="on"></span><span></span><span></span><span></span></div>
</section>

<section class="services">
  <h2 class="section-title heading">WHAT WE DO</h2>
  <p class="section-sub">Personal Training/ Fitness / Outdoor Bootcamp Class services</p>
  <div class="service-grid">
    <div class="service">
      <div class="service-icon"><svg width="64" height="40" viewBox="0 0 64 40"><rect x="2" y="14" width="6" height="12" fill="#fff"/><rect x="9" y="6" width="8" height="28" fill="#fff"/><rect x="17" y="17" width="30" height="6" fill="#fff"/><rect x="47" y="6" width="8" height="28" fill="#fff"/><rect x="56" y="14" width="6" height="12" fill="#fff"/></svg></div>
      <h3 class="service-name">PERSONAL TRAINING</h3>
      <p class="service-text">Nemo enim ipsam voluptatem quia voluptas sit aspernatur aut odit aut fugit sed quia consequuntur mag</p>
      <a class="read-more" href="#">READ MORE &gt;&gt;</a>
    </div>
    <div class="service">
      <div class="service-icon"><svg width="64" height="50" viewBox="0 0 64 50"><circle cx="32" cy="13" r="8" fill="#fff"/><circle cx="14" cy="17" r="6" fill="#fff"/><circle cx="50" cy="17" r="6" fill="#fff"/><path d="M18 46a14 14 0 0 1 28 0z" fill="#fff"/><path d="M2 44a12 12 0 0 1 18-10 18 18 0 0 0-4 10z" fill="#fff"/><path d="M62 44a12 12 0 0 0-18-10 18 18 0 0 1 4 10z" fill="#fff"/></svg></div>
      <h3 class="service-name">SMALL GROUP TRAINING</h3>
      <p class="service-text">Nemo enim ipsam voluptatem quia voluptas sit aspernatur aut odit aut fugit sed quia consequuntur mag</p>
      <a class="read-more" href="#">READ MORE &gt;&gt;</a>
    </div>
    <div class="service">
      <div class="service-icon"><svg width="62" height="52" viewBox="0 0 62 52"><rect x="4" y="4" width="44" height="30" rx="2" fill="none" stroke="#fff" stroke-width="3"/><rect x="20" y="34" width="12" height="6" fill="#fff"/><rect x="12" y="40" width="28" height="3" fill="#fff"/><circle cx="48" cy="32" r="6" fill="#fff"/><path d="M37 50a11 11 0 0 1 22 0z" fill="#fff"/></svg></div>
      <h3 class="service-name">ONLINE COACHING</h3>
      <p class="service-text">Nemo enim ipsam voluptatem quia voluptas sit aspernatur aut odit aut fugit sed quia consequuntur mag</p>
      <a class="read-more" href="#">READ MORE &gt;&gt;</a>
    </div>
    <div class="service">
      <div class="service-icon"><svg width="60" height="56" viewBox="0 0 60 56"><path d="M30 14c-8-6-22-2-22 14 0 14 10 24 22 24s22-10 22-24c0-16-14-20-22-14z" fill="#fff"/><path d="M30 14c0-5 3-9 8-11" stroke="#fff" stroke-width="3" fill="none"/><rect x="14" y="28" width="32" height="6" rx="3" fill="#0b6b3a"/></svg></div>
      <h3 class="service-name">NUTRITION PLANS</h3>
      <p class="service-text">Nemo enim ipsam voluptatem quia voluptas sit aspernatur aut odit aut fugit sed quia consequuntur mag</p>
      <a class="read-more" href="#">READ MORE &gt;&gt;</a>
    </div>
  </div>
  <div class="divider"></div>
</section>

<section class="features">
  <div class="feature-row">
    <div class="feature-photo photo-pushup" role="img" aria-label="Two women training together against a stone wall, one doing push-ups"></div>
    <div class="feature-copy">
      <h2 class="feature-title heading">PERFECT TRAINER FOR YOU</h2>
      <p class="feature-text">Nemo enim ipsam voluptatem quia voluptas sit aspernatur aut odit aut fugit, sed quia consequuntur magni dolores eos qui ratione voluptatem.</p>
      <ul class="tick-list">
        <li><svg width="12" height="12" viewBox="0 0 12 12"><circle cx="6" cy="6" r="5.3" fill="none" stroke="#888"/><path d="M3.5 6l1.8 1.8L8.7 4.3" fill="none" stroke="#888" stroke-width="1.3"/></svg>Consectetur, adipisci velit, sed quia non numquam eius modi tempora</li>
        <li><svg width="12" height="12" viewBox="0 0 12 12"><circle cx="6" cy="6" r="5.3" fill="none" stroke="#888"/><path d="M3.5 6l1.8 1.8L8.7 4.3" fill="none" stroke="#888" stroke-width="1.3"/></svg>Nemo enim ipsam voluptatem quia voluptas sit aspernatur</li>
        <li><svg width="12" height="12" viewBox="0 0 12 12"><circle cx="6" cy="6" r="5.3" fill="none" stroke="#888"/><path d="M3.5 6l1.8 1.8L8.7 4.3" fill="none" stroke="#888" stroke-width="1.3"/></svg>Ut enim ad minima veniam, quis nostrum exercitationem ullam</li>
        <li><svg width="12" height="12" viewBox="0 0 12 12"><circle cx="6" cy="6" r="5.3" fill="none" stroke="#888"/><path d="M3.5 6l1.8 1.8L8.7 4.3" fill="none" stroke="#888" stroke-width="1.3"/></svg>Quis autem vel eum iure reprehenderit qui in ea voluptate velit esse quam nihil</li>
      </ul>
      <a class="btn btn-green" href="#">Get a trainer</a>
    </div>
  </div>
  <div class="feature-row reverse">
    <div class="feature-copy">
      <h2 class="feature-title heading">BECOME A VORELAN TRAINER</h2>
      <p class="feature-text">Nemo enim ipsam voluptatem quia voluptas sit aspernatur aut odit aut fugit, sed quia consequuntur magni dolores eos qui ratione voluptatem.</p>
      <ul class="tick-list">
        <li><svg width="12" height="12" viewBox="0 0 12 12"><circle cx="6" cy="6" r="5.3" fill="none" stroke="#888"/><path d="M3.5 6l1.8 1.8L8.7 4.3" fill="none" stroke="#888" stroke-width="1.3"/></svg>Consectetur, adipisci velit, sed quia non numquam eius modi tempora</li>
        <li><svg width="12" height="12" viewBox="0 0 12 12"><circle cx="6" cy="6" r="5.3" fill="none" stroke="#888"/><path d="M3.5 6l1.8 1.8L8.7 4.3" fill="none" stroke="#888" stroke-width="1.3"/></svg>Nemo enim ipsam voluptatem quia voluptas sit aspernatur</li>
        <li><svg width="12" height="12" viewBox="0 0 12 12"><circle cx="6" cy="6" r="5.3" fill="none" stroke="#888"/><path d="M3.5 6l1.8 1.8L8.7 4.3" fill="none" stroke="#888" stroke-width="1.3"/></svg>Ut enim ad minima veniam, quis nostrum exercitationem ullam</li>
        <li><svg width="12" height="12" viewBox="0 0 12 12"><circle cx="6" cy="6" r="5.3" fill="none" stroke="#888"/><path d="M3.5 6l1.8 1.8L8.7 4.3" fill="none" stroke="#888" stroke-width="1.3"/></svg>Quis autem vel eum iure reprehenderit qui in ea voluptate velit esse quam nihil</li>
      </ul>
      <a class="btn btn-green" href="#">Read more</a>
    </div>
    <div class="feature-photo photo-couple" role="img" aria-label="Muscular man and woman posing with flexed arms on a black background"></div>
  </div>
</section>

<section class="feedback">
  <div class="feedback-bg" role="img" aria-label="Dim gym scene with a woman working out"></div>
  <div class="feedback-inner">
    <h2 class="section-title heading">WE LOVE FEEDBACK</h2>
    <div class="quotes">
      <div class="quote">
        <div class="avatar" role="img" aria-label="Portrait of Renata Solis"></div>
        <div>
          <div class="stars"><svg width="70" height="12" viewBox="0 0 70 12" fill="#f5b400"><path id="st" d="M6 0l1.8 3.9 4.2.4-3.2 2.8 1 4.1L6 9 2.2 11.2l1-4.1L0 4.3l4.2-.4z"/><use href="#st" x="14"/><use href="#st" x="28"/><use href="#st" x="42"/><use href="#st" x="56"/></svg></div>
          <p class="quote-text">“ At vero eos et accusamus et iusto odio dignissimos ducimus qui blanditiis praesen tium voluptatum deleniti atque corrupti quos dolores et quas molesti</p>
          <p class="quote-name">RENATA SOLIS</p>
        </div>
      </div>
      <div class="quote">
        <div class="avatar" role="img" aria-label="Portrait of Tobias K. Wrenfield"></div>
        <div>
          <div class="stars"><svg width="70" height="12" viewBox="0 0 70 12" fill="#f5b400"><use href="#st"/><use href="#st" x="14"/><use href="#st" x="28"/><use href="#st" x="42"/><use href="#st" x="56"/></svg></div>
          <p class="quote-text">“ At vero eos et accusamus et iusto odio dignissimos ducimus qui blanditiis praesen tium voluptatum deleniti atque corrupti quos dolores et quas molesti</p>
          <p class="quote-name">TOBIAS K. WRENFIELD</p>
        </div>
      </div>
      <div class="quote">
        <div class="avatar" role="img" aria-label="Portrait of Ines Calloway"></div>
        <div>
          <div class="stars"><svg width="70" height="12" viewBox="0 0 70 12" fill="#f5b400"><use href="#st"/><use href="#st" x="14"/><use href="#st" x="28"/><use href="#st" x="42"/><use href="#st" x="56"/></svg></div>
          <p class="quote-text">“ At vero eos et accusamus et iusto odio dignissimos ducimus qui blanditiis praesen tium voluptatum deleniti atque corrupti quos dolores et quas molesti</p>
          <p class="quote-name">INES CALLOWAY</p>
        </div>
      </div>
    </div>
  </div>
  <div class="slider-arrows">
    <span><svg width="10" height="16" viewBox="0 0 10 16"><path d="M8 2L2 8l6 6" fill="none" stroke="#555" stroke-width="2"/></svg></span>
    <span><svg width="10" height="16" viewBox="0 0 10 16"><path d="M2 2l6 6-6 6" fill="none" stroke="#555" stroke-width="2"/></svg></span>
  </div>
</section>

<section class="blog">
  <h2 class="section-title heading">VORELAN BLOG</h2>
  <div class="post-grid">
    <article class="post">
      <div class="post-photo photo-gym" role="img" aria-label="Trainer coaching a client lifting a dumbbell on a mat">
        <span class="post-date"><svg width="12" height="12" viewBox="0 0 12 12"><rect x="1" y="2" width="10" height="9" fill="none" stroke="#fff" stroke-width="1.4"/><rect x="1" y="2" width="10" height="3" fill="#fff"/></svg>12/05/2016</span>
      </div>
      <h3 class="post-title heading">Finibus Bonorum et Malorum</h3>
      <p class="post-text">Nam libero tempore, cum soluta nobis est eligendi optio cumque nihil impedit quo minus id quod maxime placeat facere possimu ssumenda est.</p>
      <a class="read-more" href="#">READ MORE &gt;&gt;</a>
    </article>
    <article class="post">
      <div class="post-photo photo-class" role="img" aria-label="Group step aerobics class in a bright studio">
        <span class="post-date"><svg width="12" height="12" viewBox="0 0 12 12"><rect x="1" y="2" width="10" height="9" fill="none" stroke="#fff" stroke-width="1.4"/><rect x="1" y="2" width="10" height="3" fill="#fff"/></svg>12/05/2016</span>
      </div>
      <h3 class="post-title heading">Finibus Bonorum et Malorum</h3>
      <p class="post-text">Nam libero tempore, cum soluta nobis est eligendi optio cumque nihil impedit quo minus id quod maxime placeat facere possimu ssumenda est.</p>
      <a class="read-more" href="#">READ MORE &gt;&gt;</a>
    </article>
    <article class="post">
      <div class="post-photo photo-outdoor" role="img" aria-label="Outdoor bootcamp group exercising with kettlebells">
        <span class="post-date"><svg width="12" height="12" viewBox="0 0 12 12"><rect x="1" y="2" width="10" height="9" fill="none" stroke="#fff" stroke-width="1.4"/><rect x="1" y="2" width="10" height="3" fill="#fff"/></svg>12/05/2016</span>
      </div>
      <h3 class="post-title heading">Finibus Bonorum et Malorum</h3>
      <p class="post-text">Nam libero tempore, cum soluta nobis est eligendi optio cumque nihil impedit quo minus id quod maxime placeat facere possimu ssumenda est.</p>
      <a class="read-more" href="#">READ MORE &gt;&gt;</a>
    </article>
  </div>
  <a class="btn btn-green" href="#">View more blog</a>
</section>

<footer class="site-footer">
  <div class="footer-brand">
    <div class="mark"></div>
    <div class="name">Vorelan</div>
  </div>
  <div class="footer-col col-info">
    <h4 class="heading">INFORMATION</h4>
    <ul><li>Home</li><li>About</li><li>Services</li><li>Blog</li><li>Videos</li><li>Contact</li></ul>
  </div>
  <div class="footer-col col-news">
    <h4 class="heading">NEWSLETTER</h4>
    <p>Register Your email address to get information about us</p>
    <div class="news-input">Email Address</div>
    <span class="news-btn">SUBSCRIBE</span>
  </div>
  <div class="footer-col col-contact">
    <h4 class="heading">CONTACT US</h4>
    <div class="contact-line"><svg width="10" height="14" viewBox="0 0 10 14"><path d="M5 0a5 5 0 0 1 5 5c0 4-5 9-5 9S0 9 0 5a5 5 0 0 1 5-5z" fill="#fff"/><circle cx="5" cy="5" r="2" fill="#1b1b1b"/></svg><span>2217 Larchmont Ave, Suite 40,<br>WA 98101 Seattle</span></div>
    <div class="contact-line"><svg width="12" height="12" viewBox="0 0 12 12"><path d="M2 0.5h2.5l1 3-1.5 1a7 7 0 0 0 3.5 3.5l1-1.5 3 1V10a1.5 1.5 0 0 1-1.5 1.5A10 10 0 0 1 .5 2 1.5 1.5 0 0 1 2 .5z" fill="#fff"/></svg><span>1 888 555 0142</span></div>
    <div class="contact-line"><svg width="13" height="10" viewBox="0 0 13 10"><rect width="13" height="10" fill="#fff"/><path d="M0 0l6.5 5.5L13 0" fill="none" stroke="#1b1b1b" stroke-width="1.2"/></svg><span>info@vorelan.com</span></div>
  </div>
  <p class="copyright">Copyrights ©2016, Vorelan. All rights reserved.</p>
  <div class="social"><span></span><span></span><span></span><span></span><span></span></div>
</footer>

</body>
</html>
```